BUSINESS CARD DESIGN

NAME- DALE VORSKIN
PHONE NUMER - 555- 714-9082
EMAIL- OFFICE@TRV-GROUNDMAKRZ.COM
BACK OF CARD- SPEACIALIZES IN LAND CLEARING, FORESTRY MUCLHING AND EXCAVATION

Contact Information for Business Card

NAME- DALE VORSKIN PHONE NUMER - 555- 714-9082 EMAIL- OFFICE@TRV-GROUNDMAKRZ.COM BACK OF CARD- SPEACIALIZES IN LAND CLEARING , MUCLHING AND EXCAVATION

```html
<!DOCTYPE html>
<html lang="en">
<head>
<meta charset="utf-8">
<title>Terravale Groundmakrz – Business Card</title>
<link rel="stylesheet" href="https://fonts.googleapis.com/css2?family=Audiowide&family=Open+Sans:wght@400;600;700&display=swap">
<style>
  :root {
    --bg: #2e2e2e;
    --card-dark: #161616;
    --card-light: #ffffff;
    --ink: #111111;
    --silver: #d9d9d9;
    --accent: #f5a900;
    --muted: #222222;
  }
  * { box-sizing: border-box; margin: 0; padding: 0; }
  html, body { width: 1200px; height: 875px; overflow: hidden; }
  body {
    background: var(--bg);
    font-family: "Open Sans", Arial, sans-serif;
    position: relative;
  }
  .card {
    position: absolute;
    width: 525px;
    height: 300px;
    border-radius: 18px;
    box-shadow: 0 18px 40px rgba(0,0,0,.45);
    overflow: hidden;
  }
  /* Back of card */
  .card--back {
    left: 60px; top: 110px;
    background: linear-gradient(160deg, #1d1d1d, var(--card-dark));
    display: flex; flex-direction: column; align-items: center; justify-content: center;
  }
  .brand { display: flex; flex-direction: column; align-items: center; gap: 12px; }
  .brand__mark {
    width: 96px; height: 96px; border-radius: 50%;
    border: 4px solid currentColor;
  }
  .brand__name {
    font-family: "Open Sans", Arial, sans-serif;
    font-weight: 700;
    font-size: 22px;
    letter-spacing: 2px;
    text-align: center;
    line-height: 1.25;
  }
  .card--back .brand { color: var(--silver); }
  .tagline {
    position: absolute; left: 0; right: 0; bottom: 28px;
    text-align: center;
    font-size: 13px; font-weight: 600; letter-spacing: .3px;
    color: var(--accent);
  }
  .tagline__lead { font-weight: 400; }

  /* Front of card */
  .card--front {
    left: 615px; top: 465px;
    background: var(--card-light);
    display: flex; align-items: center;
    padding: 0 30px;
  }
  .card--front .brand { color: var(--ink); width: 200px; }
  .card--front .brand__mark { width: 80px; height: 80px; }
  .card--front .brand__name { font-size: 17px; }
  .divider { width: 1px; height: 170px; background: var(--ink); margin: 0 24px 0 18px; }
  .contact { flex: 1; }
  .contact__name {
    font-family: "Audiowide", Arial, sans-serif;
    font-size: 25px; color: var(--ink); letter-spacing: 1px;
  }
  .contact__role { color: var(--accent); font-size: 14px; margin: 2px 0 14px; }
  .contact__list { list-style: none; }
  .contact__item {
    display: flex; align-items: flex-start; gap: 10px;
    font-size: 12.5px; color: var(--muted); line-height: 1.35; margin-bottom: 6px;
  }
  .contact__icon { width: 13px; height: 13px; flex: none; margin-top: 2px; fill: var(--accent); }
</style>
</head>
<body>

  <section class="card card--back" aria-label="Back of business card">
    <div class="brand">
      <span class="brand__mark" aria-hidden="true"></span>
      <span class="brand__name">TERRAVALE<br>GROUNDMAKRZ LLC</span>
    </div>
    <p class="tagline"><span class="tagline__lead">SPEACIALIZES IN </span>LAND CLEARING, MUCLHING &amp; EXCAVATION</p>
  </section>

  <section class="card card--front" aria-label="Front of business card">
    <div class="brand">
      <span class="brand__mark" aria-hidden="true"></span>
      <span class="brand__name">TERRAVALE<br>GROUNDMAKRZ LLC</span>
    </div>
    <span class="divider" aria-hidden="true"></span>
    <div class="contact">
      <h1 class="contact__name">DALE VORSKIN</h1>
      <p class="contact__role">Founder &amp; CEO</p>
      <ul class="contact__list">
        <li class="contact__item">
          <svg class="contact__icon" viewBox="0 0 24 24" aria-hidden="true"><path d="M12 2a7 7 0 0 0-7 7c0 5 7 13 7 13s7-8 7-13a7 7 0 0 0-7-7zm0 9.5A2.5 2.5 0 1 1 12 6.5a2.5 2.5 0 0 1 0 5z"/></svg>
          <span>423 Street Address Here, City<br>State, Country, ZIP Code</span>
        </li>
        <li class="contact__item">
          <svg class="contact__icon" viewBox="0 0 24 24" aria-hidden="true"><path d="M6.6 10.8a15 15 0 0 0 6.6 6.6l2.2-2.2a1 1 0 0 1 1-.25 11.4 11.4 0 0 0 3.6.57 1 1 0 0 1 1 1V20a1 1 0 0 1-1 1A17 17 0 0 1 3 4a1 1 0 0 1 1-1h3.5a1 1 0 0 1 1 1c0 1.25.2 2.45.57 3.6a1 1 0 0 1-.25 1z"/></svg>
          <span>555- 714-9082</span>
        </li>
        <li class="contact__item">
          <svg class="contact__icon" viewBox="0 0 24 24" aria-hidden="true"><path d="M3 5h18v14H3zm2 2v.5l7 4.5 7-4.5V7z"/></svg>
          <span>office@trv-groundmakrz.com</span>
        </li>
        <li class="contact__item">
          <svg class="contact__icon" viewBox="0 0 24 24" aria-hidden="true"><path d="M12 2a10 10 0 1 0 0 20 10 10 0 0 0 0-20zm6.9 9h-3a15 15 0 0 0-1.3-5.6A8 8 0 0 1 18.9 11zM12 4.1c.9 1.3 1.7 3.6 1.9 6.9h-3.8c.2-3.3 1-5.6 1.9-6.9zM4.1 13h3a15 15 0 0 0 1.3 5.6A8 8 0 0 1 4.1 13zm3-2h-3a8 8 0 0 1 4.3-5.6A15 15 0 0 0 7.1 11zm4.9 8.9c-.9-1.3-1.7-3.6-1.9-6.9h3.8c-.2 3.3-1 5.6-1.9 6.9zm2.6-1.3a15 15 0 0 0 1.3-5.6h3a8 8 0 0 1-4.3 5.6z"/></svg>
          <span>trv-groundmakrz.com</span>
        </li>
      </ul>
    </div>
  </section>

</body>
</html>
```